RW Framewell Inc Business cards

We need business cards using our existing logo but slightly modified. Right now the logo says RW Loadbearing Masonry. We want to keep the RW part of the design, but replace the Structural Concrete portion with "FRAMEWELL". Please see the attached file.
Ideally this would be a blank template so we can add Different Names, titles, and phone numbers later.
On the one side we want only the logo and on the other side the detail. I'm attaching an example for you to see.
Please reach out with any other questions. Our address and other details will be given out once we find a design we like.

Target Market(s)

Construction Industry

```html
<!DOCTYPE html>
<html lang="en">
<head>
<meta charset="utf-8">
<title>RW Framewell Inc — Business Cards</title>
<link href="https://fonts.googleapis.com/css2?family=Montserrat:wght@600&family=Roboto:wght@400;500&display=swap" rel="stylesheet">
<style>
  :root {
    --backdrop: #4a4a4c;
    --card: #1d1d1f;
    --brand-blue: #2f64b0;
    --text-light: #f2f2f2;
    --text-muted: #d8d8d8;
  }
  * { margin: 0; padding: 0; box-sizing: border-box; }
  html, body { width: 799px; height: 1200px; overflow: hidden; }
  body {
    background: var(--backdrop);
    font-family: "Roboto", Arial, sans-serif;
    position: relative;
  }
  .card {
    position: absolute;
    left: 80px;
    width: 640px;
    height: 366px;
    background: var(--card);
    border-radius: 6px;
  }
  .card--front { top: 120px; }
  .card--back { top: 700px; }

  .wordmark {
    position: absolute;
    display: flex;
    align-items: center;
    gap: 14px;
    font-family: "Montserrat", Arial, sans-serif;
    font-weight: 600;
    color: var(--brand-blue);
    letter-spacing: 0.06em;
    white-space: nowrap;
  }
  .wordmark__square {
    width: 22px; height: 22px;
    background: var(--brand-blue);
  }
  .card--front .wordmark {
    font-size: 44px;
    left: 50%; top: 50%;
    transform: translate(-50%, -50%);
  }
  .card--back .wordmark {
    font-size: 36px;
    left: 50%; top: 72px;
    transform: translateX(-50%);
  }

  .person {
    position: absolute;
    right: 340px;
    top: 176px;
    text-align: right;
    width: 270px;
  }
  .person__name {
    color: var(--brand-blue);
    font-weight: 500;
    font-size: 21px;
  }
  .person__title {
    color: var(--text-light);
    font-size: 15px;
    margin-top: 2px;
    padding-bottom: 7px;
    border-bottom: 1.5px solid var(--brand-blue);
  }
  .person__address {
    color: var(--text-muted);
    font-size: 14px;
    line-height: 1.45;
    margin-top: 8px;
  }

  .contacts {
    position: absolute;
    left: 330px;
    top: 232px;
    list-style: none;
  }
  .contacts li {
    display: flex;
    align-items: center;
    gap: 12px;
    color: var(--text-light);
    font-size: 15px;
    height: 24px;
  }
  .contacts svg { width: 14px; height: 14px; fill: var(--brand-blue); flex: none; }
</style>
</head>
<body>
  <section class="card card--front" aria-label="Card front">
    <div class="wordmark"><span class="wordmark__square"></span>RW Framewell</div>
  </section>

  <section class="card card--back" aria-label="Card back">
    <div class="wordmark"><span class="wordmark__square"></span>RW Framewell</div>

    <div class="person">
      <p class="person__name">John RW Smith</p>
      <p class="person__title">Managing Director</p>
      <p class="person__address">58 Sample Rd., Any Town,<br>California, US 123456</p>
    </div>

    <ul class="contacts">
      <li>
        <svg viewBox="0 0 24 24" aria-hidden="true"><path d="M6.6 10.8a15.2 15.2 0 0 0 6.6 6.6l2.2-2.2a1 1 0 0 1 1-.25 11.4 11.4 0 0 0 3.6.57 1 1 0 0 1 1 1V20a1 1 0 0 1-1 1A17 17 0 0 1 3 4a1 1 0 0 1 1-1h3.5a1 1 0 0 1 1 1c0 1.25.2 2.45.57 3.57a1 1 0 0 1-.25 1z"/></svg>
        555-010-2040
      </li>
      <li>
        <svg viewBox="0 0 24 24" aria-hidden="true"><path d="M2 5h20v14H2z M3.5 6.5 12 13l8.5-6.5" stroke="#1d1d1f" stroke-width="1.6"/></svg>
        john@framewell-example.com
      </li>
      <li>
        <svg viewBox="0 0 24 24" aria-hidden="true"><circle cx="12" cy="12" r="10"/><path d="M2 12h20M12 2c3 3 3 17 0 20M12 2c-3 3-3 17 0 20" stroke="#1d1d1f" stroke-width="1.4" fill="none"/></svg>
        www.framewell-example.com
      </li>
    </ul>
  </section>
</body>
</html>
```